Property management company looking for modern card design

We at Blue Heron Partners provides property management services for its residential and commercial properties, with expertise in all categories of multifamily, industrial and office projects throughout California.

We need a business card design that is professional and modern designed business card. In our field, clients get hundreds of business cards, we would like our card to stand out.

Please avoid small print.

Target Market(s)

Professionals and high end clients

Industry/Entity Type

Financial Planning

Contact Information for Business Card

Company Name: Blue Heron Partners, Name, email, license #, phone number, website blueheronpartners.com

Font styles to use
Sans Serif

Requirements
Must have
• The card design needs to be adaptable because there is a possibly we will be expanding into different sectors other than real estate. The card design should be focused on financial planning and asset management.
Nice to have
• Modern and simple business card. Eye catching. Non-standard size/shaped cards would be great.
• blueheronpartners.com
Should not have
• Too many bright color or any pictures or shapes of real estate stuff.

```html
<!DOCTYPE html>
<html lang="en">
<head>
<meta charset="utf-8">
<title>Blue Heron Partners — Business Card</title>
<link rel="stylesheet" href="https://fonts.googleapis.com/css2?family=Open+Sans:wght@400;600&display=swap">
<style>
  :root {
    --backdrop: #879a98;
    --card-dark: #111214;
    --card-light: #e9eeec;
    --brand-red: #c8141c;
    --ink-light: #f2f4f3;
    --ink-dark: #1a1b1c;
  }
  html, body {
    margin: 0;
    padding: 0;
    width: 1200px;
    height: 1200px;
    overflow: hidden;
    background: var(--backdrop);
  }
  .canvas {
    display: block;
    width: 1200px;
    height: 1200px;
  }
  .wordmark {
    font-family: "Open Sans", sans-serif;
    font-weight: 600;
    font-size: 40px;
    fill: var(--brand-red);
    letter-spacing: 4px;
  }
  .contact-text {
    font-family: "Open Sans", sans-serif;
    font-weight: 400;
    fill: var(--ink-light);
    font-size: 46px;
  }
  .website {
    font-family: "Open Sans", sans-serif;
    font-weight: 400;
    fill: var(--ink-dark);
    font-size: 38px;
  }
  .card-dark { fill: var(--card-dark); }
  .card-light { fill: var(--card-light); }
  .brand-dot { fill: var(--brand-red); }
  .icon-light { fill: var(--ink-light); }
  .icon-dark { fill: var(--card-dark); }
  .icon-line { fill: none; stroke: var(--card-dark); stroke-width: 3; }
</style>
</head>
<body>
<svg class="canvas" viewBox="0 0 1500 1500" xmlns="http://www.w3.org/2000/svg">

  <!-- Front of card -->
  <g class="card-front">
    <rect class="card-dark" x="63" y="269" width="651" height="1005"/>
    <circle class="brand-dot" cx="391" cy="727" r="98"/>
    <text class="wordmark" x="391" y="895" text-anchor="middle">BLUE HERON PARTNERS</text>
    <rect class="card-light base-band" x="63" y="1146" width="651" height="52"/>
  </g>

  <!-- Back of card -->
  <g class="card-back">
    <rect class="card-light" x="778" y="269" width="651" height="476"/>
    <circle class="brand-dot" cx="1108" cy="458" r="97"/>
    <text class="wordmark" x="1104" y="624" text-anchor="middle">BLUE HERON PARTNERS</text>

    <rect class="card-dark" x="778" y="745" width="651" height="345"/>

    <g class="contact-row contact-name">
      <circle class="icon-light" cx="865" cy="818" r="39"/>
      <circle class="icon-dark" cx="865" cy="808" r="10"/>
      <path class="icon-dark" d="M847,836 q0,-18 18,-18 q18,0 18,18 z"/>
      <text class="contact-text" x="940" y="826">Individual Name</text>
    </g>

    <g class="contact-row contact-phone">
      <path class="icon-light" d="M828,924 q0,-20 32,-20 q32,0 32,20 l0,6 l-14,0 l0,-8 l-36,0 l0,8 l-14,0 z"/>
      <path class="icon-light" d="M840,928 l40,0 l10,28 l-60,0 z"/>
      <g class="icon-dark">
        <circle cx="852" cy="934" r="2.5"/><circle cx="860" cy="934" r="2.5"/><circle cx="868" cy="934" r="2.5"/>
        <circle cx="852" cy="942" r="2.5"/><circle cx="860" cy="942" r="2.5"/><circle cx="868" cy="942" r="2.5"/>
        <circle cx="852" cy="950" r="2.5"/><circle cx="860" cy="950" r="2.5"/><circle cx="868" cy="950" r="2.5"/>
      </g>
      <text class="contact-text" x="940" y="945">Phone Number</text>
    </g>

    <g class="contact-row contact-email">
      <rect class="icon-light" x="828" y="1010" width="64" height="45"/>
      <polyline class="icon-line" points="830,1012 860,1038 890,1012"/>
      <line class="icon-line" x1="830" y1="1053" x2="852" y2="1032"/>
      <line class="icon-line" x1="868" y1="1032" x2="890" y2="1053"/>
      <text class="contact-text" x="940" y="1046">E-mail</text>
    </g>

    <rect class="card-light" x="778" y="1090" width="651" height="120"/>
    <text class="website" x="1104" y="1163" text-anchor="middle">www.blueheronpartners.com</text>

    <rect class="card-dark" x="778" y="1210" width="651" height="64"/>
  </g>
</svg>
</body>
</html>
```